Gaming company needs web presence

PLEASE NOTE: We need just a simple web site. We are at least a year away from launching our first product, so the site only needs a small amount of information on it. The only people who will be visiting the web site are prospective employees, prospective investors who want a little information on the company, journalists who want a little more information, and people in the games industry who will visit to read blog posts about the development of our first game.

Lanternfield Games is a new gaming company that wants to change how people think about video games. We are making games that we think can be so interesting to watch that people might want to tune into them instead of the TV.

The games we make are sophisticated, they are not for children, and we want to project an image of being serious about our craft and the brand we're trying to create. Our games are heavily focused on players interacting with each other in sophisticated ways: to negotiate, to compete, to fight, to come to each other's rescue, to cheer each other on, or to simply watch each other in awe.

We do not want a site that features lots of video game cliches like joysticks, 8 bit graphics, science fiction themes, or military themes. We are focused on craftsmanship, so we'd like to project a sense of precision, pride and deep purpose.

The purpose of this website is to create an image of our company that can help us recruit like-minded craftspeople and help find business partners. There will be no e-commerce, account creation, or forums for some time. The site should have:
-A front page that describes our business
-A section that describes our first game (we have only one for now)
-A section for employees to write blog posts. There should be something on the home page that shows links to the latest 3 blog posts.
-A section about founders that shows information about them.
-Contact information, lets people send us email

Our first game is one that looks very realistic. It takes place on a tropical island. We can't say a lot more about it in public yet, but I will say these things: it is not a game that children will play, it is not very violent, it would look more like a film than a typical video game.

And the site should be easily extendable when we have more content and more categories of content.

I've attached our official company logo with a color scheme we've been using, plus an alternate version of the logo. Please use this as a starting point for the web site's visual design. Also, I do not think it is necessary to use the dark background in the logo as the background throughout the site. I wouldn't rule it out, but I'd like to see some proposals with lighter backgrounds.

We need to be able to get code from you so that we can drop it on our server and get it running without extra effort. We need to be able to add content for Blog posts easily as well, so please indicate how that would work.
Updates

Hello everyone, Thanks for all of the great submissions so far. There are some important things I'd like to relay to everyone: We are at least a year away from launching our first game, so we only need a simple web site. Unfortunately, we can't share any screenshots or details about our first game yet. All of these submissions look great, but are far too complicated. Also, I really want to stress that we don't want to feature stock photography of people playing games, especially of children playing games. In fact, since we don't want to release any screenshots of our games and we don't have any good photography of ourselves working, it's best if there are no photographic images on the site for now.

Hello designers, Can you let me know if your designs include all the code that would let us drop the files on to our web server and easily get it up and running? Also, can you tell me how the blog posts would be created? Does your code run on a CMS? Thanks, Haskell

Hi Designers, we will be hosting this site with Wordpress, so we would prefer to have submissions ready to go on a Wordpress server. Thanks!

Target Market(s)

Investors, prospective employees, press, blog post readers.

Industry/Entity Type

Business

Font styles to use
Sans Serif

Requirements
Must have
• Simplicity first. Please use a color palette and fonts that match our logo.
Should not have
• Video game cliches. Flash animations or menus.
No children.
No photographs of people playing games.

(I realize this is very limiting, but we're keeping the sits as simple as possible for now)

```html
<!DOCTYPE html>
<html lang="en">
<head>
<meta charset="utf-8">
<title>Lanternfield Games</title>
<link href="https://fonts.googleapis.com/css2?family=Passion+One&family=Nunito+Sans:wght@400;600;700&display=swap" rel="stylesheet">
<style>
:root{
  --wood:#5b2f12;
  --wood-dark:#4a250d;
  --topbar:#6a3815;
  --footer:#7a3f15;
  --footer-dark:#5e3010;
  --orange:#e2894a;
  --heading:#cf6f33;
  --btn:#5a2c0e;
  --text:#6b6b6b;
  --rule:#e3e3e3;
  --white:#ffffff;
}
*{margin:0;padding:0;box-sizing:border-box}
html,body{width:866px;height:1200px;overflow:hidden}
body{position:relative;background:linear-gradient(90deg,var(--wood-dark),var(--wood) 20%,#623314 50%,var(--wood) 80%,var(--wood-dark));font-family:"Nunito Sans",sans-serif;color:var(--text)}
.abs{position:absolute}
.display{font-family:"Passion One",sans-serif;font-weight:400}
.topbar{left:0;top:0;width:866px;height:31px;background:var(--topbar)}
.topbar .search{left:703px;top:6px;width:110px;height:19px;background:#1f1208;color:#999;font-size:7px;font-style:italic;padding:5px 6px;border:1px solid #8a5a35}
.topbar .search svg{position:absolute;right:4px;top:4px}
.logo{left:53px;top:40px;color:#fff}
.logo .name{font-size:24px;letter-spacing:1px;font-weight:700;line-height:26px}
.logo .sub{font-size:9px;letter-spacing:4px;text-align:center;border-top:1px solid var(--orange);margin-top:2px;padding-top:1px}
.nav{left:317px;top:55px;display:flex;font-size:8.6px;color:#fff}
.nav a{color:#fff;text-decoration:none;padding:0 11px;line-height:22px}
.nav a.active{background:var(--orange);padding:0 12px}
.hero{left:54px;top:89px;width:759px;height:296px;border:2px solid #fff;background:radial-gradient(ellipse at 65% 70%,#c56a2a 0%,#5d4a3c 30%,#2f2a28 60%,#151210 100%)}
.hero h1{left:20px;top:58px;font-size:38px;color:#fff}
.hero p{left:21px;top:104px;width:330px;font-size:15px;line-height:19.5px;color:var(--orange)}
.btn{background:var(--btn);color:#fff;font-size:12px;text-align:center;letter-spacing:.5px}
.hero .more{left:21px;top:176px;width:86px;height:24px;line-height:24px}
.hero .dot{top:265px;width:8px;height:8px;border-radius:50%;background:#fff}
.panel{left:54px;top:399px;width:759px;height:578px;background:var(--white)}
.panel h2{font-size:19px;color:var(--heading);letter-spacing:.3px}
.panel .body{font-size:8.6px;line-height:16px}
.rule{height:1px;background:var(--rule)}
.ph{border:1px solid #ddd;padding:2px;background:#fff}
.ph div{width:100%;height:100%}
.list{font-size:8.6px;color:#555;list-style:none}
.list li{height:24px;position:relative;padding-left:17px}
.list li::before{content:"";position:absolute;left:0;top:4px;width:9px;height:4px;background:var(--orange);clip-path:polygon(0 25%,60% 25%,60% 0,100% 50%,60% 100%,60% 75%,0 75%)}
.founder .n{font-size:10.5px;color:#333}
.founder .d{font-size:8px;line-height:13.5px;margin-top:3px;width:150px}
.founder .c{font-size:8.5px;color:var(--orange);margin-top:10px;display:flex;align-items:center;gap:3px}
.founder .c span{margin-right:4px}
.circ{width:16px;height:16px;border-radius:50%;display:inline-block}
.post .d{font-size:8.6px;line-height:15px;width:148px}
.post .t{font-size:8.2px;color:#333;margin-top:5px}
.footer{left:0;top:977px;width:866px;height:183px;background:var(--footer)}
.bottom{left:0;top:1160px;width:866px;height:40px;background:var(--footer-dark)}
.footer h3{font-size:17px;color:var(--orange)}
.flinks{list-style:none;font-size:7.4px;color:#fff;text-transform:uppercase}
.flinks li{height:18.7px}
.field{border:1px solid #e9c1a0;color:#fff;font-size:8.6px;padding:5px 7px}
.submit{background:var(--orange);color:#fff;font-size:13px;text-align:center;line-height:28px}
.copy{left:53px;top:1177px;font-size:8px;color:var(--orange)}
.copy b{color:#fff;font-weight:400}
</style>
</head>
<body>
<header>
  <div class="abs topbar">
    <div class="abs search">Search..
      <svg width="11" height="11" viewBox="0 0 11 11"><circle cx="4.5" cy="4.5" r="3.3" fill="none" stroke="#e2894a" stroke-width="1.4"/><line x1="7" y1="7" x2="10.5" y2="10.5" stroke="#e2894a" stroke-width="1.8"/></svg>
    </div>
  </div>
  <div class="abs logo">
    <div class="name">LANTERNFIELD</div>
    <div class="sub">GAMES</div>
  </div>
  <nav class="abs nav">
    <a class="active">HOME</a><a>ABOUT US</a><a>OUR GAME</a><a>OUR FOUNDERS</a><a>BLOG</a><a>LATEST NEWS</a><a>CONTACT US</a>
  </nav>
</header>

<section class="abs hero" role="img" aria-label="Hero artwork in warm dark tones">
  <h1 class="abs display">Lorem ipsum dolor</h1>
  <p class="abs display">Sed ut perspiciatis unde omnis iste natus error sit voluptatem accusantium dolorem dantium, totam rem aperiam.</p>
  <div class="abs btn display more">LEARN MORE</div>
  <span class="abs dot" style="left:24px;background:var(--orange)"></span>
  <span class="abs dot" style="left:36px"></span>
  <span class="abs dot" style="left:47px"></span>
  <span class="abs dot" style="left:59px"></span>
</section>

<main class="abs panel">
  <h2 class="abs display" style="left:13px;top:20px">WELCOME TO OUR COMPANY WEBSITE</h2>
  <p class="abs body" style="left:13px;top:48px;width:490px">Aliquam molestie, mi et imperdiet euismod, dui purus auctor tellus, et interdum lacus lectus et ante. Sed accumsan sollicitudin sapien, sit amet adipiscing turpis gravida ac. In congue, neque ac lobortis volutpat, libero mauris varius mi, vitae suscipit ipsum ligula vitae risus. Duis aliquam nibh a dui iaculis viverra id a velit. Vivamus egestas risus in magna varius commodo. Sed semper viverra egestas. Etiam pretium porttitor lectus, vel ornare neque porta volutpat.</p>
  <div class="abs btn display" style="left:13px;top:129px;width:75px;height:24px;line-height:24px">READ MORE</div>
  <div class="abs ph" style="left:512px;top:23px;width:233px;height:130px"><div role="img" aria-label="Company image" style="background:linear-gradient(90deg,#3b3430 0%,#6e7a8a 45%,#2c3a4a 70%,#c0503a 100%)"></div></div>
  <div class="abs rule" style="left:13px;top:175px;width:732px"></div>

  <h2 class="abs display" style="left:13px;top:194px">OUR FIRST GAME</h2>
  <p class="abs body" style="left:13px;top:220px;width:480px">Aliquam molestie, mi et imperdiet euismod, dui purus auctor tellus, et interdum lacus lectus et ante. Sed accumsan sollicitudin sapien, sit amet adipiscing turpis gravida ac.</p>
  <ul class="abs list" style="left:13px;top:263px">
    <li>In congue, neque ac</li><li>Lobortis volutpat libero</li><li>Mauris varius mi vitae</li><li>Suscipit ipsum ligula vitae risus</li><li>Duis aliquam nibh</li><li>Dui iaculis viverra id a velit</li>
  </ul>
  <ul class="abs list" style="left:188px;top:263px">
    <li>Vivamus egestas risus</li><li>Magna varius commodo</li><li>Sed semper viverra egestas</li><li>Etiam pretium porttitor</li><li>Lectus &nbsp;ornare neque</li><li>Mauris et massa</li>
  </ul>
  <div class="abs ph" style="left:325px;top:261px;width:158px;height:130px"><div role="img" aria-label="Game key art" style="background:radial-gradient(circle at 50% 50%,#d8402f 0%,#e8b53a 55%,#f2d35a 100%)"></div></div>
  <div class="abs rule" style="left:13px;top:420px;width:469px"></div>
  <div class="abs" style="left:500px;top:197px;width:1px;height:360px;background:var(--rule)"></div>

  <h2 class="abs display" style="left:13px;top:437px">ABOUT OUR FOUNDERS</h2>
  <svg class="abs" style="left:465px;top:453px" width="18" height="10" viewBox="0 0 18 10"><path d="M5 1 1 5 5 9" fill="none" stroke="var(--orange)" stroke-width="2"/><path d="M13 1 17 5 13 9" fill="none" stroke="#222" stroke-width="2"/></svg>
  <div class="abs ph" style="left:13px;top:471px;width:66px;height:74px"><div role="img" aria-label="Portrait of founder" style="background:linear-gradient(#e4e4e4,#8a8a8a)"></div></div>
  <div class="abs founder" style="left:92px;top:470px">
    <div class="n">Name Goes Here</div>
    <div class="d">Aliquam molestie, mi et imperdiet euismod, dui purus auctor tellus, et interdum lacus lectus et ante...</div>
    <div class="c"><span>CONNECT:</span><i class="circ" style="background:#3b5a9a"></i><i class="circ" style="background:#3aa4dc"></i></div>
  </div>
  <div class="abs ph" style="left:259px;top:471px;width:66px;height:74px"><div role="img" aria-label="Portrait of founder" style="background:linear-gradient(#eeeeee,#7a7a7a)"></div></div>
  <div class="abs founder" style="left:338px;top:470px">
    <div class="n">Name Goes Here</div>
    <div class="d">Aliquam molestie, mi et imperdiet euismod, dui purus auctor tellus, et interdum lacus lectus et ante...</div>
    <div class="c"><span>CONNECT:</span><i class="circ" style="background:#3b5a9a"></i><i class="circ" style="background:#3aa4dc"></i></div>
  </div>

  <h2 class="abs display" style="left:518px;top:194px">BLOG POSTS</h2>
  <div class="abs ph" style="left:520px;top:224px;width:65px;height:56px"><div role="img" aria-label="Blog post thumbnail" style="background:linear-gradient(135deg,#4a6a7a,#b0803a)"></div></div>
  <div class="abs post" style="left:598px;top:220px"><div class="d">Aliquam molestie, mi et imperdiet euismod, dui purus auctor tellus, et interdum lacus lectus et ante...</div><div class="t">Posted on 3 days ago</div></div>
  <div class="abs rule" style="left:518px;top:290px;width:227px"></div>
  <div class="abs ph" style="left:520px;top:301px;width:65px;height:56px"><div role="img" aria-label="Blog post thumbnail" style="background:linear-gradient(135deg,#6a6a50,#3a3a30)"></div></div>
  <div class="abs post" style="left:598px;top:297px"><div class="d">Aliquam molestie, mi et imperdiet euismod, dui purus auctor tellus, et interdum lacus lectus et ante...</div><div class="t">Posted on 3 days ago</div></div>
  <div class="abs rule" style="left:518px;top:367px;width:227px"></div>
  <div class="abs ph" style="left:520px;top:378px;width:65px;height:56px"><div role="img" aria-label="Blog post thumbnail" style="background:linear-gradient(135deg,#5ab04a,#2a6a8a)"></div></div>
  <div class="abs post" style="left:598px;top:374px"><div class="d">Aliquam molestie, mi et imperdiet euismod, dui purus auctor tellus, et interdum lacus lectus et ante...</div><div class="t">Posted on 3 days ago</div></div>
  <div class="abs rule" style="left:518px;top:444px;width:227px"></div>
  <div class="abs ph" style="left:520px;top:455px;width:65px;height:56px"><div role="img" aria-label="Blog post thumbnail" style="background:linear-gradient(135deg,#7ac04a,#3a5a2a)"></div></div>
  <div class="abs post" style="left:598px;top:451px"><div class="d">Aliquam molestie, mi et imperdiet euismod, dui purus auctor tellus, et interdum lacus lectus et ante...</div><div class="t">Posted on 3 days ago</div></div>
  <div class="abs btn display" style="left:644px;top:536px;width:100px;height:24px;line-height:24px">READ ALL POSTS</div>
</main>

<footer>
  <div class="abs footer">
    <h3 class="abs display" style="left:53px;top:19px">COMPANY</h3>
    <ul class="abs flinks" style="left:53px;top:46px">
      <li>Home</li><li>About Us</li><li>Our Game</li><li>Our Founders</li><li>Blog</li><li>Latest News</li><li>Contact Us</li>
    </ul>
    <h3 class="abs display" style="left:181px;top:19px">OUR GAME</h3>
    <ul class="abs flinks" style="left:181px;top:46px">
      <li>In congue, neque ac</li><li>Lobortis volutpat libero</li><li>Mauris varius mi vitae</li><li>Suscipit ipsum ligula vitae risus</li><li>Duis aliquam nibh</li><li>Dui iaculis viverra id a velit</li>
    </ul>
    <h3 class="abs display" style="left:365px;top:19px">CONTACT INFO</h3>
    <div class="abs" style="left:365px;top:43px;color:#fff;font-size:7.2px;line-height:13px">
      <div style="font-size:9.6px">LANTERNFIELD GAMES</div>
      <div>412 KESTREL LANE</div>
      <div>BRIGHTMOOR, BM7 2QL</div>
      <div style="margin-top:3px">PHONE: <span style="color:var(--orange)">+1 800 555 0142</span></div>
      <div>EMAIL: <span style="color:var(--orange)">hello@lanternfieldgames.com</span></div>
    </div>
    <h3 class="abs display" style="left:365px;top:125px">CONNECT US</h3>
    <i class="abs circ" style="left:365px;top:150px;width:21px;height:21px;background:#3b5a9a;border:1px solid #fff"></i>
    <i class="abs circ" style="left:391px;top:150px;width:21px;height:21px;background:#3aa4dc;border:1px solid #fff"></i>
    <i class="abs circ" style="left:417px;top:150px;width:21px;height:21px;background:#f39a2a;border:1px solid #fff"></i>
    <i class="abs circ" style="left:443px;top:150px;width:21px;height:21px;background:#d8352a;border:1px solid #fff"></i>
    <h3 class="abs display" style="left:528px;top:19px">CONTACT US</h3>
    <div class="abs field" style="left:528px;top:48px;width:134px;height:21px">Name</div>
    <div class="abs field" style="left:678px;top:48px;width:134px;height:21px">Contact No.</div>
    <div class="abs field" style="left:528px;top:77px;width:284px;height:21px">Enter Email Address</div>
    <div class="abs field" style="left:528px;top:106px;width:205px;height:59px">Your Message</div>
    <div class="abs submit display" style="left:749px;top:137px;width:64px;height:28px">SUBMIT</div>
  </div>
  <div class="abs bottom"></div>
  <div class="abs copy">Copyright © 2014 <b>Lanternfield Games</b>. All Right Reserved</div>
</footer>
</body>
</html>
```